Tuition Center Website

We need a new web site for a tutoring company based in sydney.

We only teach senior highschool students and pride ourselves on building the students abilities to think their way through life.

I would like a bright and vibrant website that looks professional and modern.
It needs to look simple and neat but also have the functionality we need.
Images and flash would be good.

Please keep in mind that the site must be appealing to a younger audience.

We need a multipage website with the following navigation bars:

1.Home (As logo not "home" button)
I would like a news box/ticker somewhere that can stream our chatterbook and pipstream feeds and also any news updates we want to put up.
Subscribe to newsletter button.

2. About us.
This needs to be a pull down into:
-What we do
-Why we do it
-How we do it

3. Courses
Pulldown into:
-Maths
-English
-Science
(we may need to attach extra pages behind these e.g. Courses/Science/Physics or Courses/Science/Chemistry and possibly add a link to a new zandlo form)

4. Inspired
This page is like a blog page where we can upload videos, links to articles that we find to be inspiring and hopefully will inspire others.

5. Inspire
This is a recruitment page. Only content here.

6. Contact us.
Mapquill map widget and a 'contact us' form

* Our branding requires green close to #12FF3D

***Please have a look at the current website.
@ www.velmorlearning.com.au

Thanks everybody hope the revision of my brief is better and more informative than my last one

Target Market(s)

senior highschool students aged 15-19, parents ( to a lesser degree)

Industry/Entity Type

It Company

Requirements
Must have
• Ability to change content on pages.

The green doesn't have to be everywhere, but it must be obvious that it is our colour.

Nice to have
• Sites with a nicer mix of images and flash will be given more consideration. But then again, if you amaze us, you amaze us and we will go with your design.
Should not have
• Should stay away from ocre, brown colours and serif fonts.

```html
<!DOCTYPE html>
<html lang="en">
<head>
<meta charset="utf-8">
<title>Velmor Learning – Courses</title>
<link href="https://fonts.googleapis.com/css2?family=Open+Sans:wght@300;400;600;700&display=swap" rel="stylesheet">
<style>
:root{
  --green:#86e000;
  --green-dark:#6cc400;
  --green-btn:#5fa92c;
  --ink:#1c1c1c;
  --body:#3a3a3a;
  --rule:#ececec;
  --menu:#2b2b2b;
  --footer:#333;
  --white:#fff;
}
*{margin:0;padding:0;box-sizing:border-box}
html,body{width:850px;height:1200px;overflow:hidden;background:var(--white)}
body{font-family:"Open Sans",Arial,sans-serif;color:var(--body);position:relative}
.site-header{position:absolute;left:0;top:0;width:850px;height:94px;background:var(--white)}
.brand{position:absolute;left:86px;top:14px;display:flex;align-items:center;gap:8px}
.brand-mark{width:52px;height:52px;background:var(--green)}
.brand-name{font-size:15px;font-weight:600;color:var(--green-dark);line-height:1.05}
.consult{position:absolute;right:84px;top:20px;text-align:left}
.consult-row{display:flex;align-items:center;gap:6px}
.consult-label{font-size:12px;font-weight:300;color:#3a6fa0;line-height:14px;letter-spacing:-.2px}
.consult-phone{font-size:21px;font-weight:400;color:#222;margin-top:4px;letter-spacing:-.3px}
.main-nav{position:absolute;left:0;top:94px;width:850px;height:39px;background:linear-gradient(#9be81a,#79d400);border-top:1px solid #b4f04a}
.nav-item{position:absolute;top:12px;font-size:10.5px;font-weight:700;color:#3d5a10}
.nav-item.active{top:9px;left:249px;background:var(--white);color:#333;padding:3px 6px;border-radius:3px}
.follow{position:absolute;left:648px;top:12px;font-size:10px;font-weight:700;color:#4f7418;display:flex;align-items:center;gap:8px}
.social-dot{width:12px;height:12px;border-radius:50%;background:var(--white)}
.dropdown{position:absolute;left:249px;top:126px;width:78px;background:var(--menu);box-shadow:0 2px 6px rgba(0,0,0,.4);z-index:5}
.dropdown li,.submenu li{list-style:none;height:24px;line-height:24px;font-size:10.5px;color:var(--white);padding-left:11px;border-bottom:1px solid #3b3b3b;position:relative}
.dropdown li.current{color:var(--green)}
.dropdown li::after{content:"";position:absolute;right:10px;top:10px;border-left:3px solid #ccc;border-top:2px solid transparent;border-bottom:2px solid transparent}
.submenu{position:absolute;left:311px;top:180px;width:84px;background:var(--menu);box-shadow:0 2px 6px rgba(0,0,0,.4);z-index:6}
.hero{position:absolute;left:0;top:133px;width:850px;height:241px}
.hero-photo{position:absolute;inset:0;background:linear-gradient(90deg,#ececec 0%,#e4e4e4 30%,#e8c27a 42%,#b9c6d6 55%,#6fa0c8 68%,#c99aa0 82%,#8ba7c4 100%)}
.hero-title{position:absolute;left:86px;top:100px;font-size:35px;font-weight:300;color:#111;letter-spacing:-.6px}
.tagline{position:absolute;left:0;top:374px;width:850px;height:72px;background:var(--green);padding:14px 80px 0 86px}
.tagline p{font-size:15.6px;font-weight:700;color:#1d2a05;line-height:23px;letter-spacing:-.45px}
.course{position:absolute;left:85px;width:681px}
.course-head{display:flex;align-items:center;gap:12px;height:22px}
.course-head h2{font-size:18px;font-weight:700;color:var(--ink)}
.course-head span{flex:1;height:4px;background:#f0f0f0}
.course-body{display:flex;gap:21px;margin-top:17px}
.course-photo{width:178px;height:130px;flex:none}
.course-text{width:480px}
.course-text p{font-size:9.8px;line-height:14.8px;color:var(--body);margin-bottom:14.6px}
.course-text p:last-of-type{margin-bottom:0}
.btn{display:block;width:max-content;margin-top:12px;background:var(--green-btn);color:var(--white);font-size:8.5px;font-weight:600;line-height:16px;padding:0 4px;border:1px solid #4d8f1e}
.course-rule{position:absolute;left:85px;width:681px;height:1px;background:var(--rule)}
.site-footer{position:absolute;left:0;top:1157px;width:850px;height:43px;background:var(--footer);border-top:2px solid #222}
.copyright{position:absolute;left:86px;top:14px;font-size:9px;color:#eee}
.footer-nav{position:absolute;right:85px;top:14px;display:flex;gap:10px;font-size:9px;color:#eee}
</style>
</head>
<body>
<header class="site-header">
  <div class="brand"><div class="brand-mark"></div><div class="brand-name">velmor<br>learning</div></div>
  <div class="consult">
    <div class="consult-row">
      <svg width="24" height="26" viewBox="0 0 24 26" aria-hidden="true"><path d="M4 14a8 8 0 0 1 16 0" fill="none" stroke="#333" stroke-width="2"/><rect x="2" y="13" width="5" height="8" rx="2" fill="#333"/><rect x="17" y="13" width="5" height="8" rx="2" fill="#333"/><path d="M19 21q0 3-6 3" fill="none" stroke="#333" stroke-width="1.5"/></svg>
      <div class="consult-label">Call for a<br>free Consultation !</div>
    </div>
    <div class="consult-phone">555-014-2270</div>
  </div>
</header>

<nav class="main-nav">
  <span class="nav-item" style="left:97px">Home</span>
  <span class="nav-item" style="left:167px">About Us</span>
  <span class="nav-item active">Courses</span>
  <span class="nav-item" style="left:334px">Inspired</span>
  <span class="nav-item" style="left:415px">Inspire</span>
  <span class="nav-item" style="left:491px">Contact Us</span>
  <div class="follow">Follow Us <span class="social-dot"></span><span class="social-dot"></span><span class="social-dot"></span></div>
</nav>
<ul class="dropdown">
  <li>Maths</li><li>English</li><li class="current">Science</li>
</ul>
<ul class="submenu">
  <li>Physics</li><li>Chemistry</li>
</ul>

<section class="hero">
  <div class="hero-photo" role="img" aria-label="Group of smiling students holding notebooks"></div>
  <h1 class="hero-title">COURSES</h1>
</section>

<div class="tagline"><p>We’ve found that students who start with us in Year 10 have stronger foundations and are far better prepared by the time they reach Year 11 and 12.</p></div>

<article class="course" style="top:470px">
  <div class="course-head"><h2>Maths</h2><span></span></div>
  <div class="course-body">
    <div class="course-photo" role="img" aria-label="Student at a desk before a chalkboard of formulas" style="background:linear-gradient(135deg,#3f5a48,#2e4638 60%,#8a8f86)"></div>
    <div class="course-text">
      <p>Le Lorem Ipsum est simplement du faux texte employé dans la composition et la mise en page avant impression. Le Lorem Ipsum est le faux texte standard de l'imprimerie depuis les années 1500, quand un peintre anonyme assembla ensemble des morceaux de texte pour réaliser un livre spécimen de polices de texte.</p>
      <p>Il n'a pas fait que survivre cinq siècles, mais s'est aussi adapté à la bureautique informatique, sans que son contenu n'en soit modifié. Il a été popularisé dans les années 1960 grâce à la vente de feuilles Pressmark contenant des passages du Lorem Ipsum, et, plus récemment, par son inclusion dans des applications de mise en page de texte, comme Folio Layout.</p>
      <span class="btn">Know More</span>
    </div>
  </div>
</article>
<div class="course-rule" style="top:679px"></div>

<article class="course" style="top:703px">
  <div class="course-head"><h2>English</h2><span></span></div>
  <div class="course-body">
    <div class="course-photo" role="img" aria-label="Chalk writing on a blackboard" style="background:linear-gradient(135deg,#1a1a1a,#0c0c0c 70%,#2a2a2a)"></div>
    <div class="course-text">
      <p>Le Lorem Ipsum est simplement du faux texte employé dans la composition et la mise en page avant impression. Le Lorem Ipsum est le faux texte standard de l'imprimerie depuis les années 1500, quand un peintre anonyme assembla ensemble des morceaux de texte pour réaliser un livre spécimen de polices de texte.</p>
      <p>Il n'a pas fait que survivre cinq siècles, mais s'est aussi adapté à la bureautique informatique, sans que son contenu n'en soit modifié. Il a été popularisé dans les années 1960 grâce à la vente de feuilles Pressmark contenant des passages du Lorem Ipsum, et, plus récemment, par son inclusion dans des applications de mise en page de texte, comme Folio Layout.</p>
      <span class="btn">Know More</span>
    </div>
  </div>
</article>
<div class="course-rule" style="top:912px"></div>

<article class="course" style="top:935px">
  <div class="course-head"><h2>Science</h2><span></span></div>
  <div class="course-body">
    <div class="course-photo" role="img" aria-label="Young student holding books before a chalkboard" style="background:linear-gradient(135deg,#5a5a5a,#3e3e3e 60%,#6e6e6e)"></div>
    <div class="course-text">
      <p>Le Lorem Ipsum est simplement du faux texte employé dans la composition et la mise en page avant impression. Le Lorem Ipsum est le faux texte standard de l'imprimerie depuis les années 1500, quand un peintre anonyme assembla ensemble des morceaux de texte pour réaliser un livre spécimen de polices de texte.</p>
      <p>Il n'a pas fait que survivre cinq siècles, mais s'est aussi adapté à la bureautique informatique, sans que son contenu n'en soit modifié. Il a été popularisé dans les années 1960 grâce à la vente de feuilles Pressmark contenant des passages du Lorem Ipsum, et, plus récemment, par son inclusion dans des applications de mise en page de texte, comme Folio Layout.</p>
      <span class="btn">Know More</span>
    </div>
  </div>
</article>

<footer class="site-footer">
  <div class="copyright">© Velmor Learning. All rights reserved.</div>
  <div class="footer-nav"><span>Home</span><span>About Us</span><span>Courses</span><span>Inspired</span><span>Inspire</span><span>Contact Us</span></div>
</footer>
</body>
</html>
```